Anti-Grellin song (music single format) artwork

This design will be the cover art for a single that will be released on Wavorly, Zoplex, etc.
A full color cartoon or drawing is preferable, but we're open to all ideas, collages, composite images, etc. It should be interesting and satirical, but not too detailed as it will mostly be viewed as a small square on people's phone and computer screens.
The song is a high energy, musical caricature of Grellin that pokes fun of his constant threat to Paint the Sky along the US/Mexico border (among other false, idiotic or useless threats he has made). The song is literally called "Paint the Sky". Our band is against the idea of a massive US/Mexico border wall, just to be clear, and against pretty much anything that has to do with Grellin, aside from his removal from office.
The art file has to constrain to these guidelines:
1400 x 1400 pixels minimum; 3000 x 3000 pixels maximum
PNG, GIF, JPG, or JPEG file type
72 - 300dpi (300dpi is the best)
Less than 25mb
RGB color scheme (not CMYK)
Let us know if you have any questions. Thanks!
Music Download

```html
<!DOCTYPE html>
<html lang="en">
<head>
<meta charset="utf-8">
<title>Paint the Sky — single cover</title>
<link rel="stylesheet" href="https://fonts.googleapis.com/css2?family=Lilita+One&family=Permanent+Marker&display=swap">
<style>
  :root {
    --stage: #5a5c5b;
    --flag-blue: #3a4a78;
    --flag-blue-deep: #2c3760;
    --flag-red: #b8323f;
    --flag-white: #d9d4cf;
    --mx-green: #1f9a55;
    --mx-white: #e8ddd0;
    --mx-red: #d8232c;
    --shadow: rgba(10, 10, 14, 0.85);
  }
  html, body {
    margin: 0;
    padding: 0;
    width: 1200px;
    height: 812px;
    overflow: hidden;
    background: var(--stage);
  }
  .stage {
    position: relative;
    width: 1200px;
    height: 812px;
    display: flex;
    align-items: center;
    justify-content: center;
  }
  .cover {
    position: relative;
    width: 660px;
    height: 660px;
    overflow: hidden;
  }
  .cover-backdrop {
    position: absolute;
    inset: 0;
    background:
      linear-gradient(180deg,
        var(--flag-blue-deep) 0%,
        var(--flag-blue) 42%,
        var(--flag-white) 58%,
        var(--flag-red) 72%,
        var(--flag-white) 84%,
        var(--flag-red) 100%);
  }
  .cover-backdrop::after {
    content: "";
    position: absolute;
    top: 0;
    right: 0;
    width: 20%;
    height: 55%;
    background: linear-gradient(180deg, var(--flag-red), var(--flag-white) 50%, var(--flag-red));
    opacity: 0.75;
  }
  .title {
    position: absolute;
    inset: 0;
    margin: 0;
    display: flex;
    flex-direction: column;
    align-items: center;
    font-weight: 400;
    filter: drop-shadow(6px 6px 0 var(--shadow));
  }
  .title-word {
    display: block;
    background: linear-gradient(90deg,
      var(--mx-green) 0 33%,
      var(--mx-white) 33% 66%,
      var(--mx-red) 66% 100%);
    -webkit-background-clip: text;
    background-clip: text;
    color: transparent;
    line-height: 1;
  }
  .title-word--big {
    font-family: "Lilita One", "Arial Black", sans-serif;
    font-size: 132px;
    letter-spacing: 2px;
  }
  .title-word--first { margin-top: 118px; }
  .title-word--small {
    font-family: "Permanent Marker", "Comic Sans MS", cursive;
    font-size: 74px;
    margin-top: 36px;
    letter-spacing: 6px;
  }
  .title-word--last { margin-top: 36px; }
</style>
</head>
<body>
  <main class="stage">
    <section class="cover">
      <div class="cover-backdrop" role="img" aria-label="Brick wall painted with the stars and stripes of the US flag"></div>
      <h1 class="title">
        <span class="title-word title-word--big title-word--first">PAINT</span>
        <span class="title-word title-word--small">THE</span>
        <span class="title-word title-word--big title-word--last">SKY</span>
      </h1>
    </section>
  </main>
</body>
</html>
```